Business Card Design

We are a company that provides stump grinding services for residential and commercial clients. Looking for a simple business card design that may have some type of graphic on the card that will tie in with the Tamsen name(Grizzly Bear, Paw Print, etc) . Possibly some foliage wrapping around part of the card? Would like to have a simple design that stands out because it is unique. We are working on getting the website set up and there is a simple graphic on the top of the page that came to mind when I mentioned the leaves.

Industry/Entity Type

Business

Contact Information for Business Card

Tamsen Stump Grinding 303-257-4788KodiakStumps.Com

Font styles to use
Serif

Requirements
Must have
• Business name
• Website Address
• Phone Number
Nice to have
• Graphics that would be associated with a Tamsen bear.
Should not have
• Nothing frilly

```html
<!DOCTYPE html>
<html lang="en">
<head>
<meta charset="utf-8">
<title>Tamsen Stump Grinding — Business Card</title>
<link rel="stylesheet" href="https://fonts.googleapis.com/css2?family=Cinzel:wght@500&family=Open+Sans:wght@400&display=swap">
<style>
  :root {
    --backdrop: #8d8d8b;
    --card-black: #040404;
    --band-dark: #131313;
    --stripe-white: #f2f2f2;
    --stripe-grey: #6f6f6f;
    --text-white: #f4f4f4;
    --rule-grey: #4a4a4a;
    --ring-grey: #9a9a9a;
  }
  html, body {
    margin: 0;
    width: 1200px;
    height: 900px;
    overflow: hidden;
    background: var(--backdrop);
  }
  .canvas {
    width: 1200px;
    height: 900px;
    display: flex;
    align-items: center;
    justify-content: center;
  }
  .card {
    position: relative;
    width: 1000px;
    height: 572px;
    background: var(--card-black);
    overflow: hidden;
    box-shadow: 0 6px 18px rgba(0,0,0,0.25);
  }
  .band { position: absolute; left: 0; width: 100%; }
  .band--phone   { top: 330px; height: 92px;  background: var(--band-dark); }
  .band--white-a { top: 422px; height: 8px;   background: var(--stripe-white); }
  .band--grey-a  { top: 430px; height: 24px;  background: var(--stripe-grey); }
  .band--white-b { top: 454px; height: 6px;   background: var(--stripe-white); }
  .band--web     { top: 460px; height: 62px;  background: var(--band-dark); }
  .band--white-c { top: 522px; height: 10px;  background: var(--stripe-white); }
  .band--grey-b  { top: 532px; height: 40px;  background: var(--stripe-grey); }

  .brand {
    position: absolute;
    top: 110px;
    left: 170px;
    display: flex;
    align-items: center;
    gap: 34px;
  }
  .brand__ring {
    width: 96px;
    height: 96px;
    border: 3px solid var(--ring-grey);
    border-radius: 50%;
  }
  .brand__rule {
    width: 1px;
    height: 120px;
    background: var(--rule-grey);
  }
  .brand__name {
    font-family: "Cinzel", Georgia, serif;
    font-weight: 500;
    color: var(--text-white);
    line-height: 1.05;
  }
  .brand__line { display: block; font-size: 46px; letter-spacing: 1px; }
  .brand__line--wide { font-size: 40px; letter-spacing: 21px; }

  .contact {
    position: absolute;
    font-family: "Open Sans", Arial, sans-serif;
    font-size: 24px;
    color: var(--text-white);
    display: flex;
    align-items: center;
    gap: 10px;
  }
  .contact--phone { left: 60px; top: 360px; }
  .contact--web   { right: 60px; top: 474px; }
  .contact svg { width: 20px; height: 20px; fill: none; stroke: var(--text-white); stroke-width: 2; }
  .contact .icon-phone { fill: var(--text-white); stroke: none; }
</style>
</head>
<body>
<main class="canvas">
  <section class="card" aria-label="Tamsen Stump Grinding business card">
    <div class="band band--phone"></div>
    <div class="band band--white-a"></div>
    <div class="band band--grey-a"></div>
    <div class="band band--white-b"></div>
    <div class="band band--web"></div>
    <div class="band band--white-c"></div>
    <div class="band band--grey-b"></div>

    <div class="brand">
      <div class="brand__ring"></div>
      <div class="brand__rule"></div>
      <h1 class="brand__name" style="margin:0">
        <span class="brand__line">Tamsen Stump</span>
        <span class="brand__line brand__line--wide">Grinding</span>
      </h1>
    </div>

    <p class="contact contact--phone" style="margin:0">
      <svg class="icon-phone" viewBox="0 0 24 24" aria-hidden="true">
        <path d="M6.6 10.8a15.1 15.1 0 0 0 6.6 6.6l2.2-2.2a1 1 0 0 1 1-.25 11.4 11.4 0 0 0 3.6.57 1 1 0 0 1 1 1V20a1 1 0 0 1-1 1A17 17 0 0 1 3 4a1 1 0 0 1 1-1h3.5a1 1 0 0 1 1 1c0 1.25.2 2.45.57 3.57a1 1 0 0 1-.25 1z"/>
      </svg>
      <span>303-555-0146</span>
    </p>

    <p class="contact contact--web" style="margin:0">
      <span>TamsenStumps.Com</span>
      <svg viewBox="0 0 24 24" aria-hidden="true">
        <path d="M10 14a4 4 0 0 0 5.7 0l3-3a4 4 0 0 0-5.7-5.7l-1.2 1.2"/>
        <path d="M14 10a4 4 0 0 0-5.7 0l-3 3a4 4 0 0 0 5.7 5.7l1.2-1.2"/>
      </svg>
    </p>
  </section>
</main>
</body>
</html>
```